Building company buisness cards

We are looking for a sharp modern new look for our business cards.We are a New Zealand based company that specialises in house and land packages.We have attached a photo of the current logo and would like to see if it can be improved somehow if needed.We are open to any colours but we have chosen Black and White at this stage. Feel free to change the font and make the logo smarter looking.Play with the colours and see what looks best.We want a card that looks so good know one will want to throw it away!

Target Market(s)

Building profesonals, home buyers

Industry/Entity Type

Building

Contact Information for Business Card

Garrick Tenwood
0275390628
garrickt@hartvale.co.nz

Font styles to use
Serif
Sans Serif

Colors

Designer to choose colors to be used in the design.

Requirements
Must have
• Just the logo on one side and details on the other
• Clean simple looking card
Nice to have
• Round corners and detail like raised or spot UV
• Something that stands out
Should not have
• To title needed, Director etc

```html
<!DOCTYPE html>
<html lang="en">
<head>
<meta charset="utf-8">
<title>Hartvale Business Card</title>
<link rel="stylesheet" href="https://fonts.googleapis.com/css2?family=Crimson+Pro:wght@400;700&family=Roboto:wght@400&display=swap">
<style>
  :root {
    --page: #e4e4e4;
    --card: #ffffff;
    --navy: #1d2858;
    --orange: #ec9a22;
    --silver: #e6e6e6;
    --white: #ffffff;
  }
  * { margin: 0; padding: 0; box-sizing: border-box; }
  html, body {
    width: 1125px; height: 1200px; overflow: hidden;
    background: var(--page);
  }
  .card {
    position: absolute; left: 166px; width: 800px; height: 457px;
    border-radius: 22px; overflow: hidden;
    box-shadow: 2px 3px 5px rgba(0,0,0,0.35);
  }
  .card-front { top: 103px; background: var(--card); }
  .card-back { top: 619px; background: var(--orange); }

  .edge-tab {
    position: absolute; left: 0; top: 54px; width: 16px; height: 348px;
    background: var(--orange); border-radius: 0 10px 10px 0;
  }
  .brand {
    position: absolute; left: 49px; top: 178px;
    display: flex; align-items: center; gap: 12px;
  }
  .brand-name {
    font-family: "Crimson Pro", serif; font-weight: 700;
    font-size: 68px; color: var(--navy); line-height: 1;
  }
  .brand-ring {
    width: 86px; height: 86px; border-radius: 50%;
    border: 5px solid var(--orange);
  }
  .details-panel {
    position: absolute; left: 449px; top: 45px; width: 351px; height: 366px;
    background: var(--navy); border-radius: 62px 0 0 62px;
    padding: 108px 0 0 47px; color: var(--white);
  }
  .person-name {
    font-family: "Crimson Pro", serif; font-weight: 700;
    font-size: 30px; letter-spacing: 0.5px; line-height: 1;
    position: absolute; top: 108px; left: 47px; white-space: nowrap;
  }
  .contact-list {
    position: absolute; top: 177px; left: 47px; list-style: none;
    font-family: "Crimson Pro", serif; font-size: 19px; line-height: 25.5px;
  }
  .contact-list li { display: flex; align-items: center; gap: 12px; }
  .contact-list svg { width: 18px; height: 18px; fill: var(--white); flex: none; }

  .back-mark {
    position: absolute; left: 306px; top: 133px; width: 186px; height: 186px;
    border-radius: 50%; border: 7px solid var(--silver);
    display: flex; align-items: center; justify-content: center;
  }
  .back-mark-name {
    font-family: "Crimson Pro", serif; font-weight: 700;
    font-size: 34px; color: var(--silver);
  }
  .back-web {
    position: absolute; left: 0; right: 0; top: 390px; text-align: center;
    font-family: "Roboto", sans-serif; font-size: 18px;
    letter-spacing: 9px; color: var(--white);
  }
</style>
</head>
<body>
  <section class="card card-front">
    <div class="edge-tab"></div>
    <div class="brand">
      <span class="brand-name">Hartvale</span>
      <span class="brand-ring"></span>
    </div>
    <div class="details-panel">
      <h1 class="person-name">GARRICK TENWOOD</h1>
      <ul class="contact-list">
        <li>
          <svg viewBox="0 0 24 24" aria-hidden="true"><path d="M6.6 10.8c1.4 2.8 3.8 5.1 6.6 6.6l2.2-2.2c.3-.3.7-.4 1-.2 1.1.4 2.3.6 3.6.6.6 0 1 .4 1 1V20c0 .6-.4 1-1 1C10.6 21 3 13.4 3 4c0-.6.4-1 1-1h3.5c.6 0 1 .4 1 1 0 1.3.2 2.5.6 3.6.1.3 0 .7-.2 1l-2.3 2.2z"/></svg>
          <span>0275390628</span>
        </li>
        <li>
          <svg viewBox="0 0 24 24" aria-hidden="true"><path d="M2 5h20v14H2z M3.5 6.5 12 13l8.5-6.5z" fill-rule="evenodd"/></svg>
          <span>garrickt@hartvale.co.nz</span>
        </li>
        <li>
          <svg viewBox="0 0 24 24" aria-hidden="true"><path d="M12 2a10 10 0 1 0 0 20 10 10 0 0 0 0-20zm-1 3c-1 1-3 1-3 3s2 1 2 3-2 2-2 4 1 3 1 4.5A8 8 0 0 1 6 6.5C7.5 5 9 4.5 11 5zm3 14.6c0-2 2-3 2-5s-3-2-3-4 3-2 4-3.5a8 8 0 0 1-3 12.5z"/></svg>
          <span>www.hartvale.co.nz</span>
        </li>
      </ul>
    </div>
  </section>

  <section class="card card-back">
    <div class="back-mark"><span class="back-mark-name">Hartvale</span></div>
    <p class="back-web">www.Hartvale.co.nz</p>
  </section>
</body>
</html>
```